3 Business Card designs for a company with multiple services

We are a company that has 3 main services:

1) Security - CCTV & Alarm Sepcialists
2) Broadcast - Broadcast Sales and Technical Services
3) Distribution - Quality Products, Quality Service

The broadcast service is for Video Broadcast.

I will include our logos for each service.

I would like to also create a business card design for 7QR in general (see main logo).

Each card will be two-sided. On the front I would think it would include Logo, Name, Posistion and Mobile (and possibly email). And possibly our main number (which may be something like 1800 639 415)

On the back it MUST include a "lined" section to be able to write short quotes / prices.

Then include more details like Phone: 1800 639 415 Fax: 1800 639 417 Postal: PO Box 917, Tallowfield, QLD Australia 4287 Website: www.7qr.com.au

We would like a fresh, inovative card design with that "wow check this out" feel about it.

Look forward to seeing what you can do! :)

Corin

• Quote section on the back!
Editable files.

```html
<!DOCTYPE html>
<html lang="en">
<head>
<meta charset="utf-8">
<title>7QR Business Cards</title>
<link href="https://fonts.googleapis.com/css2?family=Open+Sans:wght@400;600;700&display=swap" rel="stylesheet">
<style>
  :root{
    --stage:#000;
    --ink:#5a5a5a;
    --ink-soft:#333;
    --paper:#fff;
    --sec-red:#c61f3a;
    --sec-red-dark:#a2172d;
    --sec-orange:#ee4a25;
    --sec-grey:#8a8d92;
    --bc-yellow:#f7c600;
    --bc-orange:#e0851f;
    --bc-navy:#1c2a4a;
    --mark-dark:#3b3b3b;
  }
  *{box-sizing:border-box;margin:0;padding:0}
  html,body{width:1200px;height:900px;overflow:hidden;background:var(--stage);font-family:"Open Sans",Arial,sans-serif}
  .sheet{position:relative;width:1200px;height:900px}
  .card{position:absolute;width:504px;height:290px;border-radius:14px;overflow:hidden}
  .card--front{left:74px;background:linear-gradient(160deg,#fff 45%,#ececec 100%)}
  .card--back{left:618px}
  .row-security{top:140px}
  .row-broadcast{top:466px}

  .watermark{position:absolute;left:300px;top:40px;width:180px;height:210px;border-radius:30px;
    background:radial-gradient(circle at 50% 50%,rgba(0,0,0,.05),rgba(0,0,0,.02) 70%,transparent)}

  .brand{position:absolute;display:flex;align-items:center;gap:10px;font-weight:700;font-size:22px;letter-spacing:.5px;white-space:nowrap}
  .brand__dot{width:32px;height:32px;border-radius:6px;flex:none}
  .card--front .brand{right:36px;top:48px;color:var(--mark-dark)}
  .security .brand__dot{background:var(--sec-red)}
  .broadcast .brand__dot{background:var(--bc-navy)}

  .person{position:absolute;left:28px;top:124px}
  .person__name{font-size:22px;font-weight:700;color:var(--ink)}
  .person__role{font-size:14px;color:var(--ink-soft);margin-top:4px}
  .contact{position:absolute;left:28px;top:204px;list-style:none;font-size:12px;color:var(--ink-soft);line-height:17px}
  .contact li{display:flex;align-items:center;gap:6px}
  .contact svg{width:11px;height:11px}
  .security .contact svg{fill:var(--sec-red)}
  .broadcast .contact svg{fill:#2a72b8}

  .front-band{position:absolute;left:0;right:0;bottom:0;height:16px}
  .security .front-band{background:linear-gradient(90deg,var(--sec-red) 0%,var(--sec-orange) 100%)}
  .broadcast .front-band{background:linear-gradient(90deg,var(--bc-yellow) 0%,var(--bc-orange) 100%)}

  .card--back.security{background:linear-gradient(180deg,var(--sec-red) 0%,var(--sec-red-dark) 100%)}
  .card--back.broadcast{background:linear-gradient(90deg,var(--bc-yellow) 0%,var(--bc-orange) 100%)}
  .details{position:absolute;left:22px;top:14px;font-size:12px;line-height:16px;color:#fff;width:192px}
  .divider{position:absolute;left:220px;top:16px;width:1px;height:64px;background:rgba(255,255,255,.7)}
  .card--back .brand{left:250px;top:28px;color:#fff;font-size:21px}
  .card--back.security .brand__dot{background:#fff}
  .card--back.broadcast .brand__dot{background:var(--bc-navy)}
  .note{position:absolute;left:16px;right:22px;top:94px;height:142px;background:var(--paper);border-radius:18px;padding:8px 12px}
  .note__label{font-size:14px;font-weight:700;color:#222}
  .site{position:absolute;left:0;right:0;top:244px;text-align:center;font-size:12px;letter-spacing:2px;color:#fff}
  .back-band{position:absolute;left:0;right:0;bottom:0;height:24px}
  .security .back-band{background:linear-gradient(180deg,#c7c8cb,var(--sec-grey))}
  .broadcast .back-band{background:linear-gradient(180deg,#3a4a6e,var(--bc-navy))}
</style>
</head>
<body>
<main class="sheet">
  <svg width="0" height="0" style="position:absolute">
    <symbol id="icon-phone" viewBox="0 0 12 12"><path d="M3 1h2l1 3-1.5 1a6 6 0 0 0 2.5 2.5L8 6l3 1v2a2 2 0 0 1-2 2A8 8 0 0 1 1 3a2 2 0 0 1 2-2z"/></symbol>
    <symbol id="icon-mail" viewBox="0 0 12 12"><path d="M1 3h10v7H1z M1 3l5 4 5-4"/></symbol>
  </svg>

  <section class="card card--front security row-security">
    <div class="watermark" role="img" aria-label="Faint service emblem decoration"></div>
    <div class="brand"><span class="brand__dot"></span>7QR Security</div>
    <div class="person"><p class="person__name">Sam Tully</p><p class="person__role">Field Manager</p></div>
    <ul class="contact">
      <li><svg><use href="#icon-phone"/></svg>200 300 5186</li>
      <li><svg><use href="#icon-phone"/></svg>1800 639 415</li>
      <li><svg><use href="#icon-mail"/></svg>sam@7qr.com.au</li>
    </ul>
    <div class="front-band"></div>
  </section>

  <section class="card card--back security row-security">
    <div class="details">Phone: 1800 639 415<br>Fax: 1800 639 417<br>Postal: PO Box 917, Tallowfield,<br>QLD Australia 4287</div>
    <div class="divider"></div>
    <div class="brand"><span class="brand__dot"></span>7QR Security</div>
    <div class="note"><p class="note__label">Note :</p></div>
    <p class="site">www.7qr.com.au</p>
    <div class="back-band"></div>
  </section>

  <section class="card card--front broadcast row-broadcast">
    <div class="watermark" role="img" aria-label="Faint service emblem decoration"></div>
    <div class="brand"><span class="brand__dot"></span>7QR Broadcast</div>
    <div class="person"><p class="person__name">Sam Tully</p><p class="person__role">Field Manager</p></div>
    <ul class="contact">
      <li><svg><use href="#icon-phone"/></svg>200 300 5186</li>
      <li><svg><use href="#icon-phone"/></svg>1800 639 415</li>
      <li><svg><use href="#icon-mail"/></svg>sam@7qr.com.au</li>
    </ul>
    <div class="front-band"></div>
  </section>

  <section class="card card--back broadcast row-broadcast">
    <div class="details">Phone: 1800 639 415<br>Fax: 1800 639 417<br>Postal: PO Box 917, Tallowfield,<br>QLD Australia 4287</div>
    <div class="divider"></div>
    <div class="brand"><span class="brand__dot"></span>7QR Broadcast</div>
    <div class="note"><p class="note__label">Note :</p></div>
    <p class="site">www.7qr.com.au</p>
    <div class="back-band"></div>
  </section>
</main>
</body>
</html>
```